A layout of a webpage for oil trade platform

I would like to have a desgin of one page webpage (with section scrollling dowin) that woulf present the new product i.e. oil trade platform for wholesale buyers and sellers.
Layout should consist of the sections similar to the given at: https://porada.leczmypol.pl/panel-planowania-spotkan
However oil industy require more colors and more photo stories than here for doctor.
I. I woul imagine at first below menu a slider with brueg information about the product and its advantages with "more" button next to the prict screen of our platform on different displays (PC and mobile).
II. Bellow the slider I would imagine icons correspoing to the advantages of that plaftorm:
1. Purchase/sale process automation 24/7
2. Access to the best deals
3. Electronic offerings and orderings
4. Transaction status monitoring
5. Data and transaction security
II A) (optional):
In near future we would like to prepare a short video presenation. Hence please prepare a place to display that element here.
At the moment alternatvily please prepare a How it works section that would explan the platform operating process
III. Next secion is about benefits for Oil Purchaser
It can be done either by icons of by text and corresponding grahip for while section.
Benefits:
- Access to cheaper oil
- Convenience of online orders
- Possibility to compare prices on the market
- Transaction history
- Order status monitoring
- Seccurity and transparency of purchase
IV. Next seciont is about benefits for Oil Seller
Benefits:
- New sale channel
- Attracting new clients
- More oil sold
- Transaction security
- Possibility to integrate with distribution infrastructure and logistits for more efficient automation.
V. Contact form
VI. Footer
I would need a layout that that will correspond to the very dynamic logo but I would expect also a clean form, smoth and modern. It has to be proffessional layout with more corporate character.
It can use a paralax features if needed.

```html
<!DOCTYPE html>
<html lang="en">
<head>
<meta charset="utf-8">
<title>Crudeline – Oil Trade Platform</title>
<link href="https://fonts.googleapis.com/css2?family=Roboto:wght@300;400;500;700&display=swap" rel="stylesheet">
<style>
:root{
  --navy:#14213f;
  --navy-deep:#0f1a35;
  --orange:#f26a1b;
  --orange-light:#f8923a;
  --page:#efeff1;
  --white:#ffffff;
  --ink:#1d2333;
  --muted:#8a8f9c;
  --line:#d6d8de;
}
*{box-sizing:border-box;margin:0;padding:0}
html,body{width:1200px;height:4296px;overflow:hidden}
body{background:var(--page);font-family:'Roboto',sans-serif;color:var(--ink);position:relative}
.abs{position:absolute}

/* nav */
.nav{left:0;top:0;width:1200px;height:60px;z-index:5}
.brand{left:118px;top:18px;display:flex;align-items:center;gap:8px;color:var(--white);font-weight:500;font-size:14px}
.brand-dot{width:18px;height:18px;border-radius:50%;background:var(--orange)}
.nav-link{top:17px;font-size:11px;color:#c7cbd6;white-space:nowrap}
.nav-signin{left:994px;top:11px;width:84px;height:26px;background:var(--orange);color:var(--white);font-size:12px;font-weight:500;display:flex;align-items:center;justify-content:center;border-radius:2px}

/* hero */
.hero-bg{left:0;top:0;width:1200px;height:560px}
.hero-title{left:120px;top:122px;font-size:40px;font-weight:400;color:var(--white);letter-spacing:.3px}
.hero-sub{left:120px;top:182px;width:540px;font-size:17px;line-height:25px;font-weight:300;color:#b9c4e3}
.hero-btn{left:120px;top:258px;width:132px;height:37px;background:var(--orange);color:var(--white);font-size:11px;font-weight:500;letter-spacing:.5px;display:flex;align-items:center;justify-content:center;border-radius:2px}
.hero-devices{left:660px;top:86px;width:460px;height:320px;border-radius:10px;background:linear-gradient(150deg,#eef1f6 0%,#c9ced8 55%,#9aa1ae 100%)}

/* section heads */
.eyebrow{font-size:10px;letter-spacing:1px;text-transform:uppercase;color:var(--muted)}
.section-title{font-size:22px;font-weight:400}
.dash{width:22px;height:2px;background:var(--orange)}
.center{left:0;width:1200px;text-align:center}

/* advantages */
.adv{top:779px;width:200px;text-align:center}
.adv-icon{width:63px;height:63px;margin:0 auto;background:linear-gradient(160deg,var(--orange-light),var(--orange));border-radius:3px;display:flex;align-items:center;justify-content:center}
.adv-label{margin-top:18px;font-size:14px;line-height:21px;font-weight:500;color:var(--ink)}

.photo-refinery{left:0;top:945px;width:1200px;height:573px;background:linear-gradient(180deg,var(--page) 0%,#d9cdbd 18%,#e8c79b 40%,#cdb79b 62%,#e4e1dc 85%,var(--page) 100%)}

/* how it works */
.hiw-eyebrow{left:122px;top:1680px}
.hiw-title{left:122px;top:1705px;font-size:22px;line-height:30px;font-weight:400}
.hiw-text{left:122px;top:1806px;width:370px;font-size:12px;line-height:19px;color:var(--muted)}
.video-frame{left:533px;top:1612px;width:538px;height:350px;background:var(--white);box-shadow:0 12px 34px rgba(20,33,63,.18)}
.video-bar{height:22px;background:#f4f4f6;display:flex;align-items:center;gap:6px;padding-left:12px}
.video-bar i{width:7px;height:7px;border-radius:50%;display:block}
.video-area{position:absolute;left:10px;top:28px;right:10px;bottom:10px;background:linear-gradient(135deg,#6f7f4b,#a99a5a 45%,#5b6470)}
.play{position:absolute;left:50%;top:50%;width:70px;height:70px;margin:-35px 0 0 -35px;border-radius:50%;background:var(--orange);display:flex;align-items:center;justify-content:center}

/* purchaser */
.purchaser-bg{left:0;top:1900px;width:1200px;height:830px}
.pur-eyebrow{top:2146px;color:#8e97b2}
.pur-title{top:2168px;color:var(--white)}
.benefit{width:320px;text-align:center}
.benefit-icon{width:48px;height:48px;margin:0 auto;border-radius:4px;background:var(--white);display:flex;align-items:center;justify-content:center}
.benefit-name{margin-top:18px;font-size:13px;line-height:19px;font-weight:500;color:var(--white)}
.benefit-text{margin-top:6px;font-size:12px;line-height:19px;color:#a6aec6}

/* seller */
.tablet{left:172px;top:2792px;width:400px;height:330px;border-radius:14px;background:linear-gradient(150deg,#f7f8fa,#d9dde4 55%,#aeb4bf)}
.sel-eyebrow{left:607px;top:2826px}
.sel-title{left:607px;top:2850px;font-size:24px;line-height:33px;font-weight:400}
.sel-text{left:607px;top:2950px;width:560px;font-size:12px;line-height:19px;color:var(--muted)}
.sel-feature{top:3044px;width:80px;text-align:center;font-size:10px;line-height:14px;color:var(--muted)}
.sel-feature svg{display:block;margin:0 auto 8px}

.photo-truck{left:0;top:3179px;width:1200px;height:630px;background:linear-gradient(180deg,var(--page) 0%,#b5bdc7 22%,#8d959e 48%,#9e7a5c 64%,#7c8189 80%,#c9ccd1 100%)}

/* contact */
.contact{left:235px;top:3715px;width:730px;height:366px;background:var(--white);box-shadow:0 10px 30px rgba(20,33,63,.12)}
.field{position:absolute;border:1px solid var(--line);font-size:11px;color:var(--muted);padding:11px 12px}
.submit{position:absolute;left:295px;top:286px;width:132px;height:37px;background:var(--orange);color:var(--white);font-size:11px;font-weight:500;display:flex;align-items:center;justify-content:center;border-radius:2px}

/* footer */
.foot-brand{left:0;width:1200px;top:4098px;display:flex;justify-content:center;align-items:center;gap:8px;font-size:14px;font-weight:500;color:var(--navy)}
.socials{left:0;width:1200px;top:4210px;display:flex;justify-content:center;gap:10px}
.socials span{width:17px;height:17px;background:var(--navy);display:block}
.copy{top:4246px;font-size:9px;line-height:14px;color:var(--muted)}
</style>
</head>
<body>

<!-- hero -->
<svg class="abs hero-bg" viewBox="0 0 1200 560" aria-hidden="true">
  <path d="M0 0H1200V250C1110 330 1040 300 930 380C820 460 690 460 560 410C430 360 330 390 230 440C150 480 70 470 0 430Z" fill="var(--navy)"/>
  <path d="M0 360C70 400 140 420 230 400C330 380 440 320 560 330C700 340 820 470 960 420C1060 385 1120 320 1200 280V300C1120 345 1060 410 960 445C820 495 700 370 560 360C440 352 330 412 230 432C140 450 70 430 0 392Z" fill="var(--orange)"/>
  <circle cx="158" cy="428" r="30" fill="var(--orange)" opacity=".25" stroke="var(--orange)" stroke-opacity=".5"/>
  <circle cx="1050" cy="300" r="26" fill="var(--orange)" opacity=".25"/>
  <circle cx="452" cy="520" r="32" fill="var(--orange)" opacity=".18"/>
</svg>

<nav class="abs nav">
  <div class="abs brand"><span class="brand-dot"></span>Crudeline</div>
  <span class="abs nav-link" style="left:687px">Advantages</span>
  <span class="abs nav-link" style="left:767px">How it Works</span>
  <span class="abs nav-link" style="left:853px">Benefits</span>
  <span class="abs nav-link" style="left:914px">Contact Us</span>
  <div class="abs nav-signin">Sign in</div>
</nav>

<h1 class="abs hero-title">New Oil Trade Platform</h1>
<p class="abs hero-sub">User-friendly and mobile Crudeline that allows you<br>to give your customers the level of service they expect</p>
<div class="abs hero-btn">LEARN MORE</div>
<div class="abs hero-devices" role="img" aria-label="Platform dashboard shown on a laptop and a phone"></div>

<!-- advantages -->
<p class="abs center eyebrow" style="top:652px">Advantages</p>
<h2 class="abs center section-title" style="top:672px">The Advantges of the Best Oil Trade Platform</h2>
<div class="abs dash" style="left:589px;top:719px"></div>

<div class="abs adv" style="left:106px"><div class="adv-icon"><svg width="28" height="28" viewBox="0 0 28 28" fill="none" stroke="#fff" stroke-width="2"><circle cx="14" cy="14" r="5"/><path d="M14 3v4M14 21v4M3 14h4M21 14h4M6 6l3 3M19 19l3 3M6 22l3-3M19 9l3-3"/></svg></div><p class="adv-label">Purchase/sale process<br>automation 24/7</p></div>
<div class="abs adv" style="left:310px"><div class="adv-icon"><svg width="28" height="28" viewBox="0 0 28 28" fill="none" stroke="#fff" stroke-width="2"><circle cx="18" cy="10" r="6"/><path d="M14 14L5 23M8 20l3 3"/></svg></div><p class="adv-label">Access to the best<br>deals</p></div>
<div class="abs adv" style="left:501px"><div class="adv-icon"><svg width="28" height="28" viewBox="0 0 28 28" fill="none" stroke="#fff" stroke-width="2"><path d="M5 7h3M5 14h3M5 21h3M12 7h11M12 14h11M12 21h11"/></svg></div><p class="adv-label">Electronic offerings<br>and orderings</p></div>
<div class="abs adv" style="left:696px"><div class="adv-icon"><svg width="28" height="28" viewBox="0 0 28 28" fill="none" stroke="#fff" stroke-width="2"><rect x="6" y="6" width="16" height="16" rx="2" transform="rotate(45 14 14)"/><path d="M10 14l3 3 5-6"/></svg></div><p class="adv-label">Transaction status<br>monitoring</p></div>
<div class="abs adv" style="left:891px"><div class="adv-icon"><svg width="28" height="28" viewBox="0 0 28 28" fill="none" stroke="#fff" stroke-width="2"><rect x="6" y="12" width="16" height="12" rx="1"/><path d="M9 12V8a5 5 0 0110 0v4M14 16v4"/></svg></div><p class="adv-label">Data and transaction<br>security</p></div>

<div class="abs photo-refinery" role="img" aria-label="Oil refinery with spherical storage tanks at sunset"></div>

<!-- how it works -->
<p class="abs hiw-eyebrow eyebrow">How it works</p>
<h2 class="abs hiw-title">Earn Money doing<br>the Least Amount of Work</h2>
<p class="abs hiw-text">When you trade oil with Crudeline you're not actually buying any physical oil. Instead, you enter into a contract related to the real price of the commodity. This type of trade is known as a Contract For Difference, or CFD.</p>

<svg class="abs purchaser-bg" viewBox="0 0 1200 830" aria-hidden="true">
  <path d="M0 110C120 100 220 150 320 140C460 125 560 70 700 80C860 92 960 40 1040 0H1200V830H0Z" fill="var(--navy)"/>
  <path d="M0 92C120 82 220 130 320 120C460 106 560 50 700 62C860 76 960 22 1030 -10L1045 -10C965 34 860 100 700 94C560 88 460 146 320 160C220 170 120 122 0 114Z" fill="var(--orange)"/>
  <circle cx="178" cy="108" r="34" fill="var(--orange)" opacity=".22" stroke="var(--orange)" stroke-opacity=".5"/>
  <circle cx="520" cy="100" r="40" fill="var(--orange)" opacity=".22" stroke="var(--orange)" stroke-opacity=".5"/>
  <circle cx="1045" cy="10" r="28" fill="var(--orange)" opacity=".2"/>
</svg>

<div class="abs video-frame">
  <div class="video-bar"><i style="background:#ee5b4e"></i><i style="background:#f3b542"></i><i style="background:#5cc26a"></i></div>
  <div class="video-area" role="img" aria-label="Video presentation of the platform, team meeting around a laptop">
    <div class="play"><svg width="26" height="28" viewBox="0 0 26 28"><path d="M4 2L24 14L4 26Z" fill="#fff"/></svg></div>
  </div>
</div>

<!-- purchaser benefits -->
<p class="abs center eyebrow pur-eyebrow">For oil purchaser</p>
<h2 class="abs center section-title pur-title">Here's a list of our Awesome Benefits</h2>
<div class="abs dash" style="left:589px;top:2212px"></div>

<div class="abs benefit" style="left:115px;top:2272px"><div class="benefit-icon"><svg width="24" height="24" viewBox="0 0 24 24" fill="none" stroke="var(--orange)" stroke-width="1.8"><circle cx="12" cy="12" r="8"/><path d="M12 8v8M9 10h5M9 14h5"/></svg></div><p class="benefit-name">Access to cheaper oil</p><p class="benefit-text">Lorem ipsum dolor sit amet, nec summo<br>menandri appellantur id, eos te amet simul.</p></div>
<div class="abs benefit" style="left:440px;top:2272px"><div class="benefit-icon"><svg width="24" height="24" viewBox="0 0 24 24" fill="none" stroke="var(--orange)" stroke-width="1.8"><rect x="4" y="5" width="16" height="13" rx="1"/><path d="M8 21h8M8 12l3 3 5-5"/></svg></div><p class="benefit-name">Order status monitoring</p><p class="benefit-text">Lorem ipsum dolor sit amet, nec summo<br>menandri appellantur id, eos te amet simul.</p></div>
<div class="abs benefit" style="left:765px;top:2272px"><div class="benefit-icon"><svg width="24" height="24" viewBox="0 0 24 24" fill="none" stroke="var(--orange)" stroke-width="1.8"><path d="M5 6h2M5 12h2M5 18h2M10 6h9M10 12h9M10 18h9"/></svg></div><p class="benefit-name">Transaction history</p><p class="benefit-text">Lorem ipsum dolor sit amet, nec summo<br>menandri appellantur id, eos te amet simul.</p></div>

<div class="abs benefit" style="left:115px;top:2470px"><div class="benefit-icon"><svg width="24" height="24" viewBox="0 0 24 24" fill="none" stroke="var(--orange)" stroke-width="1.8"><path d="M12 4v16M5 8h14M5 8l-2 6h4zM19 8l-2 6h4zM8 20h8"/></svg></div><p class="benefit-name">Possibility to compare<br>prices on the market</p><p class="benefit-text">Lorem ipsum dolor sit amet, nec summo<br>menandri appellantur id, eos te amet simul.</p></div>
<div class="abs benefit" style="left:440px;top:2470px"><div class="benefit-icon"><svg width="24" height="24" viewBox="0 0 24 24" fill="none" stroke="var(--orange)" stroke-width="1.8"><circle cx="12" cy="12" r="8"/><path d="M8.5 14a4 4 0 007 0M9 10h.01M15 10h.01"/></svg></div><p class="benefit-name">Convenience of<br>online orders</p><p class="benefit-text">Lorem ipsum dolor sit amet, nec summo<br>menandri appellantur id, eos te amet simul.</p></div>
<div class="abs benefit" style="left:765px;top:2470px"><div class="benefit-icon"><svg width="24" height="24" viewBox="0 0 24 24" fill="none" stroke="var(--orange)" stroke-width="1.8"><path d="M12 3l7 3v5c0 5-3 8-7 10-4-2-7-5-7-10V6z"/><path d="M9 12l2 2 4-4"/></svg></div><p class="benefit-name">Security and transparency<br>of purchase</p><p class="benefit-text">Lorem ipsum dolor sit amet, nec summo<br>menandri appellantur id, eos te amet simul.</p></div>

<!-- seller -->
<div class="abs tablet" role="img" aria-label="Platform dashboard with charts on a tablet"></div>
<p class="abs sel-eyebrow eyebrow">For oil seller</p>
<h2 class="abs sel-title">Organize your<br>Business Fast &amp; Easily</h2>
<div class="abs dash" style="left:607px;top:2926px"></div>
<p class="abs sel-text">Lorem ipsum dolor sit amet, persim graeci in sum. Has ne talens aliquid. Sed illud modo recteque ea, duo quodsi iudicabit te his duo mnesarchum. Fugit atque audiam pro cu, ex soret accusam sed.</p>

<div class="abs sel-feature" style="left:590px"><svg width="24" height="24" viewBox="0 0 24 24" fill="none" stroke="var(--orange)" stroke-width="1.6"><path d="M4 10h16v10H4zM4 10l2-5h12l2 5M10 14h4"/></svg>New sale<br>channel</div>
<div class="abs sel-feature" style="left:678px"><svg width="24" height="24" viewBox="0 0 24 24" fill="none" stroke="var(--orange)" stroke-width="1.6"><path d="M3 12l4-4 5 3 5-3 4 4-9 7z"/></svg>Attracting new<br>clients</div>
<div class="abs sel-feature" style="left:766px"><svg width="24" height="24" viewBox="0 0 24 24" fill="none" stroke="var(--orange)" stroke-width="1.6"><path d="M12 3c4 6 6 9 6 12a6 6 0 01-12 0c0-3 2-6 6-12z"/></svg>More oil<br>sold</div>
<div class="abs sel-feature" style="left:854px"><svg width="24" height="24" viewBox="0 0 24 24" fill="none" stroke="var(--orange)" stroke-width="1.6"><rect x="5" y="11" width="14" height="10" rx="1"/><path d="M8 11V8a4 4 0 018 0v3"/></svg>Transaction<br>security</div>
<div class="abs sel-feature" style="left:942px"><svg width="24" height="24" viewBox="0 0 24 24" fill="none" stroke="var(--orange)" stroke-width="1.6"><path d="M7 18a4 4 0 010-8 6 6 0 0111 2 3 3 0 010 6z"/></svg>Possibility to<br>integrate</div>

<div class="abs photo-truck" role="img" aria-label="Orange tanker truck driving on a road under a cloudy sky"></div>
<svg class="abs" style="left:0;top:3640px" width="1200" height="240" viewBox="0 0 1200 240" aria-hidden="true">
  <path d="M0 160C90 120 170 150 240 130V146C170 166 90 140 0 178Z" fill="var(--orange)"/>
  <path d="M960 60C1040 40 1110 90 1200 60V74C1110 104 1040 56 960 76Z" fill="var(--orange)"/>
</svg>

<!-- contact -->
<section class="abs contact">
  <p class="abs eyebrow" style="left:0;width:730px;text-align:center;top:36px">Contact us</p>
  <h2 class="abs section-title" style="left:0;width:730px;text-align:center;top:58px">If you've got Any Questions, Mail Us</h2>
  <div class="abs dash" style="left:354px;top:96px"></div>
  <div class="field" style="left:52px;top:108px;width:310px;height:37px">Your Name</div>
  <div class="field" style="left:376px;top:108px;width:302px;height:37px">Your Email</div>
  <div class="field" style="left:52px;top:160px;width:626px;height:108px">Your Message</div>
  <div class="submit">SUBMIT</div>
</section>

<!-- footer -->
<footer>
  <div class="abs foot-brand"><span class="brand-dot"></span>Crudeline</div>
  <div class="abs socials"><span></span><span></span><span></span><span></span><span></span></div>
  <p class="abs center copy">© 2017 Copyright · Crudeline<br>All Rights Reserved</p>
</footer>

</body>
</html>
```